Tour operator needs simple coded WordPress site (updated extra payment for coding and guaranteed)

[update 9/7/2015]
If you design a new logo and it gets accepted, even if we use another template with your logo you will get $50
[update 8/7/2015]
Update on questions about dual-language
For dual languages we are happy to set up a second site with the same designs in a second language.
For the design aspect just allow the user to switch between languages with an icon.
For the coding, a replica of the site on a second server will do (to save messing around with multiple language plugins) - we will populate it with Chinese text
[original post]
Simple coded WordPress site for tours
You can choose to design only or design and code ($340 design, $150 bonus for coding)
Open design brief - use your creativity
Will be in 2 languages (English and Chinese) but design needs only to be in one language
Winning design will be chosen only from home page, but the winner must make a second standard template page when chosen at no extra cost.
Must be responsive design
We only need homepage and standard template page design and coding, we will populate the pages
You can use design ideas from our pamphlet if you like - attached
Only a sample logo and colors on website and pamphlet - feel free to change as the current ones seem restrictive
Current website framework only to give an idea of the number of pages and basic menu structure (no need to use existing navigation style or any style at all for that matter, open brief)
http://brightwattlejourneys.com.au/
Target Market(s)
Chinese parents of kids 10-14 (the kids will take the tour)
Industry/Entity Type
Tour
Number of Pages Required
2 page
Look and feel
Each slider illustrates characteristics of the customer's brand and the style your logo design should communicate.

```html
<!DOCTYPE html>
<html lang="en">
<head>
<meta charset="utf-8">
<title>Bright Wattle Journeys</title>
<link rel="stylesheet" href="https://fonts.googleapis.com/css2?family=Oswald:wght@400;500&family=Lato:wght@400;700&display=swap">
<style>
:root{
  --navy:#2f3f86;
  --navy-band:#35468c;
  --gold:#f0b323;
  --ink:#2b2b2b;
  --grey-text:#5a5a5a;
  --rule:#c9c9c9;
  --panel:#efefef;
  --footer:#1e1e1e;
  --white:#ffffff;
}
*{box-sizing:border-box;margin:0;padding:0}
html,body{width:926px;height:1200px;overflow:hidden;background:var(--white)}
body{font-family:'Lato',sans-serif;color:var(--grey-text);position:relative}
.heading{font-family:'Oswald',sans-serif;font-weight:400;color:var(--ink);letter-spacing:-.2px}

/* hero */
.hero{position:absolute;left:0;top:0;width:926px;height:476px}
.hero-photo{position:absolute;inset:0;background:
  radial-gradient(ellipse at 45% 55%, rgba(190,90,70,.55) 0%, rgba(160,70,60,0) 45%),
  radial-gradient(ellipse at 80% 20%, rgba(150,160,175,.7) 0%, rgba(150,160,175,0) 55%),
  linear-gradient(180deg,#7a8597 0%,#5b6372 45%,#3e3a3c 100%)}
.lang{position:absolute;left:748px;top:15px;width:77px;height:24px;border:2px solid var(--white);color:var(--white);font-size:12px;font-weight:700;padding:3px 0 0 9px}
.lang svg{position:absolute;right:9px;top:7px}
.slide-arrow{position:absolute;top:200px}
.slide-arrow.prev{left:62px}
.slide-arrow.next{left:826px}
.brand-box{position:absolute;left:102px;top:304px;width:216px;height:109px;background:var(--white);display:flex;align-items:center;justify-content:center;gap:8px}
.brand-box .dot{width:14px;height:14px;border-radius:50%;background:var(--gold)}
.brand-box .name{font-family:'Lato',sans-serif;font-weight:700;font-size:16px;color:var(--navy);text-transform:uppercase;line-height:1.2;text-align:left}
.tagline{position:absolute;right:101px;top:360px;width:460px;text-align:right;font-family:'Oswald',sans-serif;font-size:21px;line-height:28px;color:var(--white);text-transform:uppercase}
.nav-bar{position:absolute;left:0;top:429px;width:926px;height:47px;border-top:1px solid rgba(255,255,255,.35);background:rgba(30,30,35,.25)}
.nav{position:absolute;left:102px;top:0;display:flex;height:47px;list-style:none}
.nav li{font-size:12px;font-weight:700;color:var(--white);display:flex;align-items:center;justify-content:center;height:47px}
.nav li.current{background:var(--white);color:var(--navy)}
.social{position:absolute;left:713px;top:8px;display:flex;gap:9px}
.social span{width:31px;height:31px;border:2px solid var(--white);border-radius:50%}

/* welcome */
.welcome{position:absolute;left:0;top:476px;width:926px;height:257px}
.intro{position:absolute;left:102px;top:46px;width:455px}
.intro h1{font-size:22px;line-height:28px;padding-bottom:3px;border-bottom:1px solid var(--rule)}
.intro h1 .navy{color:var(--navy)}
.intro h1 .gold{color:var(--gold)}
.intro .lead{margin-top:8px;font-size:11.5px;font-weight:700;line-height:15px;color:var(--grey-text)}
.intro p{font-size:10px;line-height:13.5px;margin-top:5px}
.btn{display:inline-block;background:var(--navy);color:var(--white);font-weight:700;font-size:13px;text-align:center;width:105px;height:26px;line-height:26px;text-transform:uppercase}
.intro .btn{position:absolute;right:0;top:168px}
.divider{position:absolute;left:575px;top:30px;width:1px;height:210px;background:#dcdcdc}
.inquiry{position:absolute;left:598px;top:46px;width:227px}
.inquiry h2{font-size:22px;line-height:28px}
.field{border:1px solid #b9b9b9;height:26px;margin-top:7px;font-size:11px;color:#8a8a8a;padding:6px 7px}
.inquiry h2 + .field{margin-top:11px}
.field.message{height:58px}
.inquiry .btn{position:absolute;right:0;top:168px}

/* features */
.features{position:absolute;left:0;top:733px;width:926px;height:380px;background:var(--panel)}
.card{position:absolute;top:38px;width:347px;height:305px;background:var(--white);border:1px solid #d6d6d6;border-top:2px solid var(--gold);padding:14px 15px 0 13px}
.card.edu{left:102px}
.card.safe{left:478px}
.card-head{display:flex;align-items:flex-end;gap:6px;margin-bottom:8px}
.card-head h3{flex:1;font-family:'Oswald',sans-serif;font-weight:400;font-size:17px;color:var(--navy);line-height:22px;border-bottom:1px dotted #9a9a9a;text-transform:uppercase}
.card ul{list-style:none}
.card li{position:relative;padding-left:24px;font-size:10px;line-height:13px;margin-bottom:8px}
.card.safe li{margin-bottom:6px}
.card li svg{position:absolute;left:2px;top:0}

/* newsletter */
.newsletter{position:absolute;left:0;top:1113px;width:926px;height:44px;background:var(--navy-band);color:var(--white)}
.newsletter .icon{position:absolute;left:102px;top:5px}
.newsletter .title{position:absolute;left:145px;top:9px;font-size:19px}
.newsletter .chev{position:absolute;left:344px;top:3px}
.newsletter .note{position:absolute;left:390px;top:14px;font-size:11.5px}
.newsletter .email{position:absolute;left:572px;top:11px;width:187px;height:22px;background:var(--white);color:#333;font-size:10px;padding:5px 7px}
.newsletter .go{position:absolute;left:767px;top:11px;width:58px;height:22px;background:#111;border:1px solid #555;font-size:10px;font-weight:700;text-align:center;line-height:20px}

/* footer */
.site-footer{position:absolute;left:0;top:1157px;width:926px;height:43px;background:var(--footer);color:var(--white);font-size:10px}
.site-footer .links{position:absolute;left:102px;top:16px}
.site-footer .copy{position:absolute;right:103px;top:16px}
</style>
</head>
<body>

<header class="hero">
  <div class="hero-photo" role="img" aria-label="Photo of a smiling group of students on a riverside ferry wharf with a steel bridge behind"></div>
  <div class="lang">English
    <svg width="11" height="7" viewBox="0 0 11 7"><path d="M1 1l4.5 4.5L10 1" fill="none" stroke="#fff" stroke-width="1.8"/></svg>
  </div>
  <svg class="slide-arrow prev" width="40" height="78" viewBox="0 0 40 78"><path d="M38 1L2 39l36 38" fill="none" stroke="#fff" stroke-width="1.3"/></svg>
  <svg class="slide-arrow next" width="40" height="78" viewBox="0 0 40 78"><path d="M2 1l36 38L2 77" fill="none" stroke="#fff" stroke-width="1.3"/></svg>
  <div class="brand-box"><span class="dot"></span><span class="name">Bright Wattle<br>Journeys</span></div>
  <div class="tagline">Educational, safe, culturally Australian. Bright Wattle Journeys enlightening and fun.</div>
  <nav class="nav-bar">
    <ul class="nav">
      <li class="current" style="width:111px">Home</li>
      <li style="width:128px">About Us</li>
      <li style="width:68px">Tours</li>
      <li style="width:100px;margin-left:12px">Contact Us</li>
    </ul>
    <div class="social"><span></span><span></span><span></span></div>
  </nav>
</header>

<section class="welcome">
  <div class="intro">
    <h1 class="heading">WELCOME TO <span class="navy">BRIGHT</span> <span class="gold">WATTLE</span> <span class="navy">JOURNEYS</span></h1>
    <p class="lead">At Bright Wattle Journeys we are passionate about educational travel and opportunities for students to gain academic and cultural understanding of Australia.</p>
    <p>14 day premium cultural and educational tours to Australian cities. Educational, safe, culturally enlightening and fun. Learn about educational institutions, history, sports, laws and customs, food and culture while improving your English.</p>
    <p>At Bright Wattle Journeys we are passionate about educational travel and providing opportunities for students to learn more about a country and gain a deeper understanding of the culture. The out of classroom experience gained on our trips is invaluable.</p>
    <span class="btn">Read More</span>
  </div>
  <div class="divider"></div>
  <div class="inquiry">
    <h2 class="heading">QUICK INQUIRY</h2>
    <div class="field">Name</div>
    <div class="field">Email</div>
    <div class="field message">Message</div>
    <span class="btn">Submit</span>
  </div>
</section>

<section class="features">
  <article class="card edu">
    <div class="card-head">
      <svg width="30" height="22" viewBox="0 0 30 22"><path d="M15 3L1 9l14 6 14-6z" fill="#f0b323"/><path d="M7 12v5c0 2 4 3.5 8 3.5s8-1.5 8-3.5v-5l-8 3.5z" fill="#f0b323"/><path d="M27 10v7" stroke="#f0b323" stroke-width="1.5"/></svg>
      <h3>Educational and Cultural</h3>
    </div>
    <ul>
      <li><svg width="18" height="12" viewBox="0 0 18 12"><path d="M1 11C3 5 8 4 12 4V1l5 5-5 5V7.5C8 7.5 4 8 1 11z" fill="#2f3f86"/></svg>Professional lecturers from Sydney universities</li>
      <li><svg width="18" height="12" viewBox="0 0 18 12"><path d="M1 11C3 5 8 4 12 4V1l5 5-5 5V7.5C8 7.5 4 8 1 11z" fill="#2f3f86"/></svg>2 hour lessons every day in easy to understand,<br>high-quality English</li>
      <li><svg width="18" height="12" viewBox="0 0 18 12"><path d="M1 11C3 5 8 4 12 4V1l5 5-5 5V7.5C8 7.5 4 8 1 11z" fill="#2f3f86"/></svg>Subjects from the Australian Educational Curriculum as well as cultural information on Australia</li>
      <li><svg width="18" height="12" viewBox="0 0 18 12"><path d="M1 11C3 5 8 4 12 4V1l5 5-5 5V7.5C8 7.5 4 8 1 11z" fill="#2f3f86"/></svg>How to live, get around, shop and socialise in Australia</li>
      <li><svg width="18" height="12" viewBox="0 0 18 12"><path d="M1 11C3 5 8 4 12 4V1l5 5-5 5V7.5C8 7.5 4 8 1 11z" fill="#2f3f86"/></svg>Attitudes to languages, food, religion and culture</li>
      <li><svg width="18" height="12" viewBox="0 0 18 12"><path d="M1 11C3 5 8 4 12 4V1l5 5-5 5V7.5C8 7.5 4 8 1 11z" fill="#2f3f86"/></svg>Outdoor activities and sport</li>
    </ul>
  </article>
  <article class="card safe">
    <div class="card-head">
      <svg width="30" height="24" viewBox="0 0 30 24"><path d="M8 11V7a5 5 0 0 1 10 0v1" fill="none" stroke="#f0b323" stroke-width="2.5"/><rect x="4" y="10" width="18" height="13" rx="2" fill="#f0b323"/><circle cx="13" cy="16" r="2" fill="#fff"/></svg>
      <h3>Safe and Secure</h3>
    </div>
    <ul>
      <li><svg width="18" height="12" viewBox="0 0 18 12"><path d="M1 11C3 5 8 4 12 4V1l5 5-5 5V7.5C8 7.5 4 8 1 11z" fill="#2f3f86"/></svg>Staff certified by the government for Working With Children</li>
      <li><svg width="18" height="12" viewBox="0 0 18 12"><path d="M1 11C3 5 8 4 12 4V1l5 5-5 5V7.5C8 7.5 4 8 1 11z" fill="#2f3f86"/></svg>Staff certified in first aid care</li>
      <li><svg width="18" height="12" viewBox="0 0 18 12"><path d="M1 11C3 5 8 4 12 4V1l5 5-5 5V7.5C8 7.5 4 8 1 11z" fill="#2f3f86"/></svg>Professional accommodation with excellent history in caring for children with extremely well documented Safety Management Procedures including;</li>
      <li><svg width="18" height="12" viewBox="0 0 18 12"><path d="M1 11C3 5 8 4 12 4V1l5 5-5 5V7.5C8 7.5 4 8 1 11z" fill="#2f3f86"/></svg>Safety Management - reducing risk when taking students out of the classroom</li>
      <li><svg width="18" height="12" viewBox="0 0 18 12"><path d="M1 11C3 5 8 4 12 4V1l5 5-5 5V7.5C8 7.5 4 8 1 11z" fill="#2f3f86"/></svg>Safety &amp; Emergency Procedures (Location-specific)</li>
      <li><svg width="18" height="12" viewBox="0 0 18 12"><path d="M1 11C3 5 8 4 12 4V1l5 5-5 5V7.5C8 7.5 4 8 1 11z" fill="#2f3f86"/></svg>Standard Operating Procedures</li>
      <li><svg width="18" height="12" viewBox="0 0 18 12"><path d="M1 11C3 5 8 4 12 4V1l5 5-5 5V7.5C8 7.5 4 8 1 11z" fill="#2f3f86"/></svg>Activity-Specific Risk Management Matrix</li>
      <li><svg width="18" height="12" viewBox="0 0 18 12"><path d="M1 11C3 5 8 4 12 4V1l5 5-5 5V7.5C8 7.5 4 8 1 11z" fill="#2f3f86"/></svg>Area Assessment Documentation</li>
      <li><svg width="18" height="12" viewBox="0 0 18 12"><path d="M1 11C3 5 8 4 12 4V1l5 5-5 5V7.5C8 7.5 4 8 1 11z" fill="#2f3f86"/></svg>Medical Form, Dietary Requirements Form ,First Aid Incident &amp; Management Forms</li>
      <li><svg width="18" height="12" viewBox="0 0 18 12"><path d="M1 11C3 5 8 4 12 4V1l5 5-5 5V7.5C8 7.5 4 8 1 11z" fill="#2f3f86"/></svg>Clothing &amp; Equipment List</li>
    </ul>
  </article>
</section>

<section class="newsletter">
  <svg class="icon" width="34" height="34" viewBox="0 0 34 34"><circle cx="17" cy="17" r="15.5" fill="none" stroke="#fff" stroke-width="2"/><rect x="9" y="11" width="16" height="12" rx="1" fill="#fff"/><path d="M9.5 11.5L17 18l7.5-6.5M9.5 22.5l5.5-5M24.5 22.5l-5.5-5" fill="none" stroke="#35468c" stroke-width="1.3"/></svg>
  <span class="title">Newsletter Signup</span>
  <svg class="chev" width="30" height="38" viewBox="0 0 30 38"><path d="M2 2l16 17L2 36M10 2l16 17-16 17" fill="none" stroke="#fff" stroke-width="1.3"/></svg>
  <span class="note">Signup For Free Email Updates</span>
  <div class="email">Enter your email here</div>
  <div class="go">SUBMIT</div>
</section>

<footer class="site-footer">
  <div class="links">Home &nbsp;|&nbsp; About Us &nbsp;|&nbsp; Tours &nbsp;|&nbsp; Contact Us</div>
  <div class="copy">© 2015 BRIGHT WATTLE JOURNEYS. &nbsp;|&nbsp; All Rights Reserved.</div>
</footer>

</body>
</html>
```